Business Card - connecting 2 souls and beggining the journey of self discovery

Logo on the front
with tag line

On the back list of services and contact details

Seminars
workshops
Coaching
podcasts

Darren Whitlow
Health & Wellbeing Life Coach
0491 372 615
darren@brightcoreliving.example
brightcoreliving.example

Industry/Entity Type

Life Coaching

Contact Information for Business Card

I like the use of colour from the logo to be used. I'm not a fan of white.

Requirements
Must have
• My tagline: The journey home starts with you
Nice to have
• Use of colour that is in the mind body soul logo

```html
<!DOCTYPE html>
<html lang="en">
<head>
<meta charset="utf-8">
<title>Brightcore Living — Business Card</title>
<link rel="stylesheet" href="https://fonts.googleapis.com/css2?family=Roboto+Slab:wght@400;500&family=Kaushan+Script&display=swap">
<style>
  :root {
    --purple: #8e55a3;
    --yellow: #f6dc3f;
    --pink: #f06075;
    --teal: #38b2a6;
    --green: #98c94f;
    --orange: #f47b57;
    --charcoal: #3a3a3c;
    --paper: #fcfcfc;
    --ink-grey: #6b6b6d;
    --backdrop: #2b2b2d;
    --slab: "Roboto Slab", Georgia, serif;
    --script: "Kaushan Script", cursive;
  }
  * { box-sizing: border-box; margin: 0; padding: 0; }
  html, body { width: 1200px; height: 800px; overflow: hidden; }
  body { background: var(--backdrop); position: relative; font-family: var(--slab); }

  .card {
    position: absolute;
    top: 240px;
    width: 530px;
    height: 310px;
    border-radius: 18px;
    overflow: hidden;
  }
  .card--front { left: 50px; background: var(--paper); }
  .card--back { left: 620px; background: var(--charcoal); }

  /* colour bands */
  .band { position: absolute; left: 0; right: 0; display: flex; }
  .band span { flex: 1; }
  .band--top { top: 0; height: 30px; }
  .band--bottom { bottom: 0; height: 40px; }
  .c-purple { background: var(--purple); }
  .c-yellow { background: var(--yellow); }
  .c-pink { background: var(--pink); }
  .c-teal { background: var(--teal); }
  .c-green { background: var(--green); }
  .c-orange { background: var(--orange); }

  /* front content */
  .swoosh { position: absolute; left: 0; top: 0; width: 530px; height: 310px; }
  .brand {
    position: absolute; top: 42px; left: 0; right: 0;
    display: flex; flex-direction: column; align-items: center;
  }
  .brand__mark {
    width: 52px; height: 52px; border-radius: 50%;
    background: var(--teal);
  }
  .brand__name {
    margin-top: 6px; font-size: 20px; font-weight: 500;
    color: var(--ink-grey); letter-spacing: -0.3px;
  }
  .brand__web {
    font-size: 14px; color: var(--orange); margin-top: 1px;
  }
  .holder__name {
    position: absolute; top: 140px; left: 0; right: 0;
    text-align: center; font-family: var(--script);
    font-size: 46px; color: var(--orange); line-height: 1;
  }
  .holder__role {
    position: absolute; top: 204px; left: 50%; transform: translateX(-50%);
    padding: 3px 6px; border-top: 1.5px solid var(--orange); border-bottom: 1.5px solid var(--orange);
    font-size: 14px; color: var(--orange); letter-spacing: 0.3px; white-space: nowrap;
  }
  .holder__contact {
    position: absolute; top: 236px; left: 0; right: 0;
    text-align: center; font-size: 17px; color: var(--orange);
  }

  /* back content */
  .services {
    position: absolute; top: 0; left: 0; right: 0; height: 238px;
    display: flex; list-style: none;
  }
  .services li {
    flex: 1; position: relative;
  }
  .services li span {
    position: absolute; left: 50%; top: 50%;
    transform: translate(-50%, -50%) rotate(-90deg);
    font-size: 22px; white-space: nowrap;
  }
  .on-yellow { color: #8a7a1c; }
  .on-pink { color: #7a2a3c; }
  .on-teal { color: #17544e; }
  .on-green { color: #2f6a26; }
  .tagline {
    position: absolute; left: 0; right: 0; bottom: 0; height: 72px;
    display: flex; align-items: center; justify-content: center;
    color: #fff; font-size: 20px;
  }
</style>
</head>
<body>

<section class="card card--front" aria-label="Business card front">
  <div class="band band--top">
    <span class="c-purple"></span><span class="c-yellow"></span><span class="c-pink"></span>
    <span class="c-teal"></span><span class="c-green"></span><span class="c-orange"></span>
  </div>

  <svg class="swoosh" viewBox="0 0 530 310" aria-hidden="true">
    <path d="M0 112 C40 112 60 150 90 152 C120 154 140 150 160 150" fill="none" stroke="var(--orange)" stroke-width="2"/>
    <path d="M380 172 C420 160 470 168 530 205" fill="none" stroke="var(--orange)" stroke-width="2"/>
  </svg>

  <div class="brand">
    <div class="brand__mark"></div>
    <div class="brand__name">Brightcore Living</div>
    <div class="brand__web">www.brightcoreliving.example</div>
  </div>

  <div class="holder__name">Darren Whitlow</div>
  <div class="holder__role">HEALTH &amp; WELLBEING LIFE COACH</div>
  <div class="holder__contact">0491 372 615 | darren@brightcoreliving.example</div>

  <div class="band band--bottom">
    <span class="c-purple"></span><span class="c-yellow"></span><span class="c-pink"></span>
    <span class="c-teal"></span><span class="c-green"></span><span class="c-orange"></span>
  </div>
</section>

<section class="card card--back" aria-label="Business card back">
  <ul class="services">
    <li class="c-purple"></li>
    <li class="c-yellow"><span class="on-yellow">Seminars</span></li>
    <li class="c-pink"><span class="on-pink">Workshops</span></li>
    <li class="c-teal"><span class="on-teal">Coaching</span></li>
    <li class="c-green"><span class="on-green">Podcasts</span></li>
    <li class="c-orange"></li>
  </ul>
  <p class="tagline">The journey home starts with you</p>
</section>

</body>
</html>
```